Bright Harbor Counseling Letterhead for hip modern business

I would like some ombre use of the colors in the logo hip letterhead that incorporates logo colors and feel, needs to connect with young professionals and college students. i need to be able to write letters to schools to excuse absences as well. i like color blocks on one side preferably using colors from the attached logo design.

Target Market(s)

high income young people, young adults and college students

Industry/Entity Type

mental health

Font styles to use
Serif
Sans Serif

Colors
0054AA
0677BA
7BADD7
CADEEF
E8F1F8
0094D4
00A9DD
6FCCEA
C7EBF8
E9F6FB
00AB8E
00BBA5
67D7C9
C6EFE9
E9F9F6
59FF00
82FF00
B8FF75
E3FFCB
F4FFEA
A7469A
B969AE
D3A5CF
EDDBEB
F8F0F9
6B429C
8869AF
B7A5CE
E3DAEB
F3F0F8

Requirements
Must have
• a modern hip feel, somewhat color

```html
<!DOCTYPE html>
<html lang="en">
<head>
<meta charset="utf-8">
<title>Bright Harbor Counseling Letterhead</title>
<link href="https://fonts.googleapis.com/css2?family=Open+Sans:wght@300;400;700&display=swap" rel="stylesheet">
<style>
  :root {
    --paper: #ffffff;
    --backdrop: #dfe3e4;
    --magenta-deep: #a7469a;
    --magenta: #b969ae;
    --magenta-soft: #d3a5cf;
    --magenta-pale: #eddbeb;
    --ink: #3c3c44;
    --ink-soft: #6a6a72;
    --rule: #c9c9cf;
  }
  * { margin: 0; padding: 0; box-sizing: border-box; }
  html, body {
    width: 1200px; height: 784px; overflow: hidden;
    background: var(--backdrop);
  }
  .letterhead {
    position: relative;
    width: 1200px; height: 784px;
    background: var(--paper);
    font-family: "Open Sans", sans-serif;
    overflow: hidden;
  }
  .header-band {
    position: absolute; left: 0; top: 0;
    width: 1200px; height: 70px;
  }
  .brand {
    position: absolute; top: 40px; right: 90px;
    color: var(--ink);
    font-weight: 300;
  }
  .brand-name {
    display: flex; align-items: center; gap: 14px;
    font-size: 34px; line-height: 1.1; letter-spacing: 0.5px;
  }
  .brand-dot {
    width: 30px; height: 30px; border-radius: 50%;
    background: var(--magenta);
  }
  .brand-sub {
    font-size: 17px; letter-spacing: 4px;
    margin-left: 60px; margin-top: 4px;
  }
  .contact {
    position: absolute; right: 0; top: 290px;
    width: 300px; height: 160px;
  }
  .contact-rule {
    position: absolute; left: 0; top: 0;
    width: 150px; height: 1px; background: var(--rule);
  }
  .side-block {
    position: absolute; right: 0; top: 10px;
    width: 8px; height: 140px;
    background: linear-gradient(180deg, var(--magenta-deep), var(--magenta-soft) 60%, var(--magenta-pale));
  }
  .contact-list {
    position: absolute; left: 28px; top: 16px;
    list-style: none; font-size: 12.5px; line-height: 1.55;
    color: var(--ink-soft);
  }
  .contact-list li { display: flex; align-items: flex-start; gap: 8px; }
  .contact-list svg { flex: none; margin-top: 3px; }
  .contact-address { color: var(--magenta-deep); font-weight: 700; }
</style>
</head>
<body>
<main class="letterhead">
  <svg class="header-band" viewBox="0 0 1200 70" aria-hidden="true">
    <defs>
      <linearGradient id="band-ombre" x1="0" y1="0" x2="1" y2="0">
        <stop offset="0" stop-color="#eddbeb"/>
        <stop offset="0.35" stop-color="#d3a5cf"/>
        <stop offset="0.7" stop-color="#b969ae"/>
        <stop offset="1" stop-color="#a7469a"/>
      </linearGradient>
      <linearGradient id="band-sheen" x1="0" y1="0" x2="0" y2="1">
        <stop offset="0" stop-color="#ffffff" stop-opacity="0.25"/>
        <stop offset="1" stop-color="#ffffff" stop-opacity="0"/>
      </linearGradient>
    </defs>
    <path d="M0 0 H1200 V22 H1120 V28 Q1120 34 1114 34 H0 Z" fill="url(#band-ombre)"/>
    <path d="M0 0 H880 V22 Q880 40 862 40 H0 Z" fill="url(#band-ombre)"/>
    <path d="M0 34 H880 V40 Q880 54 866 54 H0 Z" fill="url(#band-ombre)" opacity="0.85"/>
    <rect x="0" y="0" width="1200" height="22" fill="url(#band-sheen)"/>
    <rect x="0" y="52" width="860" height="2" fill="#ffffff" opacity="0.6"/>
  </svg>

  <header class="brand">
    <div class="brand-name">Bright Harbor <span class="brand-dot"></span></div>
    <div class="brand-sub">Counseling</div>
  </header>

  <aside class="contact">
    <span class="contact-rule"></span>
    <span class="side-block"></span>
    <ul class="contact-list">
      <li class="contact-address">
        <svg width="11" height="11" viewBox="0 0 12 12" aria-hidden="true"><circle cx="6" cy="6" r="6" fill="#a7469a"/><path d="M6 2.5a2.2 2.2 0 0 0-2.2 2.2C3.8 6.4 6 9.5 6 9.5s2.2-3.1 2.2-4.8A2.2 2.2 0 0 0 6 2.5z" fill="#fff"/></svg>
        <span>0000 Harbor Way, Ste 210,<br>California, 93100, United States</span>
      </li>
      <li>
        <svg width="11" height="11" viewBox="0 0 12 12" aria-hidden="true"><circle cx="6" cy="6" r="6" fill="#a7469a"/><path d="M4 3l1.2 1.4-.6.8c.5 1 1.2 1.7 2.2 2.2l.8-.6L9 8l-.8 1C5.5 8.7 3.3 6.5 3 3.8z" fill="#fff"/></svg>
        <span>(000) 000-0000</span>
      </li>
      <li>
        <svg width="11" height="11" viewBox="0 0 12 12" aria-hidden="true"><circle cx="6" cy="6" r="6" fill="#a7469a"/><rect x="3.5" y="4" width="5" height="4" fill="#fff"/></svg>
        <span>(000) 000-0000</span>
      </li>
      <li>
        <svg width="11" height="11" viewBox="0 0 12 12" aria-hidden="true"><circle cx="6" cy="6" r="6" fill="#a7469a"/><rect x="3" y="4" width="6" height="4.2" rx="0.6" fill="#fff"/><path d="M3 4.3 6 6.5l3-2.2" stroke="#a7469a" stroke-width="0.7" fill="none"/></svg>
        <span>info@brightharbor.com</span>
      </li>
      <li>
        <svg width="11" height="11" viewBox="0 0 12 12" aria-hidden="true"><circle cx="6" cy="6" r="6" fill="#a7469a"/><circle cx="6" cy="6" r="3" fill="none" stroke="#fff" stroke-width="0.9"/><path d="M3 6h6M6 3v6" stroke="#fff" stroke-width="0.7"/></svg>
        <span>www.brightharbor.com</span>
      </li>
    </ul>
  </aside>
</main>
</body>
</html>
```